Corwin Beacon Lighting - Commercial & Residential Landscape Lighting

Landscape Lighting Services & Design: Create a website for our landscape lighting company. We would like the design to be tailored around this description:
Illuminate with Confidence. Designed with Precision. Installed with Care.
Locally and veteran-owned, we take pride in transforming outdoor spaces through innovative lighting solutions tailored to your vision. From landscape and holiday lighting to permanent installations, our effortless process and expert design deliver breathtaking results and lasting curb appeal. Backed by a lifetime warranty and quarterly service options, our commitment to quality and customer satisfaction is unwavering. Try before you buy and experience your home in a whole new light with our complimentary demo kit — see the stunning effects before you decide.
- Also, add in this information as well; Outdoor Lighting not only beautifies spaces but also significantly enhances safety by illuminating your home or business. Beautifully lit entrances deter potential intruders, making your home a safer place for your loved ones. we also offer quarterly service plans to ensure lighting equipment continues to operate & illuminate effectively throughout the year. Also mention we provide free estimates and we are offering a 10% discount to military, veterans, and first responders.

Target Market(s)

Luxury market

Industry/Entity Type

Landscape Lighting - Residential & Commercial Lighting Services

Coding

Coded - Design and coding required

Number of Pages Required

2 page

Colors
00AB8E
00BBA5
67D7C9
C6EFE9
E9F9F6
59FF00
82FF00
B8FF75
E3FFCB
F4FFEA
FFC000
F8CF3A
FAE287
FDF2CF
FEFAEE

Requirements
Must have
• a lead generation button where people can submit their information for us to reach out to them and schedule their free estimate, homepage, about page, contact page, products and services page, user friendly, easy to navigate, and it also must be engaging and eye popping, as well as appealing to the luxury market. Please use colors; verdent green, dark green, ivory, and sunny yellow. Also, include an about page that references our story; Derek is retired Army and he opened a fitness studio in 2017 with his wife Jolene. He has installed low voltage lighting in every home he lived in and for his friends and family over the years and decided to open his own business because he is passionate about beautifying outdoor landscapes and highlighting a properties full potential, not only in the day but at night as well all while providing safety and security for his clients. Having a deep respect for nature and landscaping, he wants to provide the same care and quality to each of his clients as he has in the fitness industry for decades. He believes small businesses are the back bone of America and he's excited to provide a service that is all to often neglected in the design of a home.
Nice to have
• I would like to have a clear intent and purpose, engaging web design, clear call to action, optimized for search engines, mobile friendy design, security measures, credibility indicators

```html
<!DOCTYPE html>
<html lang="en">
<head>
<meta charset="utf-8">
<title>Corwin Beacon Lighting – Residential Landscape Lighting</title>
<link href="https://fonts.googleapis.com/css2?family=Montserrat:wght@400;500;600;700;800&display=swap" rel="stylesheet">
<style>
:root{
  --green:#1d9371;
  --green-dark:#14744f;
  --yellow:#ffc000;
  --yellow-soft:#f8cf3a;
  --ivory:#fdf8ea;
  --navy:#22194d;
  --ink:#1b1b1b;
  --mist:#ecebf1;
  --white:#ffffff;
}
*{margin:0;padding:0;box-sizing:border-box}
html,body{width:1200px;height:4431px;overflow:hidden}
body{font-family:"Montserrat",sans-serif;color:var(--ink);background:var(--white);position:relative}
.abs{position:absolute}
.btn{position:absolute;display:flex;align-items:center;justify-content:center;background:var(--yellow);color:var(--ink);font-weight:800;font-size:14px;letter-spacing:.2px;text-transform:uppercase;text-decoration:none}
.btn-outline{position:absolute;display:flex;align-items:center;justify-content:center;border:2px solid var(--green);color:var(--green);font-weight:700;font-size:13px;background:var(--white);text-transform:uppercase}
.photo{position:absolute}
.rule{position:absolute;width:36px;height:3px;background:var(--navy)}
/* hero */
.hero{position:absolute;left:0;top:0;width:1200px;height:671px;background:linear-gradient(180deg,#1d2a4a 0%,#2c3a55 35%,#3a3a33 62%,#4a4a30 80%,#2c3320 100%)}
.brand{position:absolute;color:var(--white);font-weight:500;letter-spacing:2px;display:flex;align-items:center;gap:10px}
.nav{position:absolute;top:38px;left:420px;display:flex;align-items:center;gap:28px;color:var(--white);font-size:14px;font-weight:500}
.nav .active{background:var(--yellow);color:var(--ink);padding:6px 13px;font-weight:700}
.hero-title{position:absolute;left:0;width:1200px;text-align:center;color:var(--white);font-weight:800}
/* intro */
.intro-head{position:absolute;left:625px;top:752px;font-size:29px;font-weight:800;line-height:41px;color:var(--ink)}
.intro-head span{color:var(--yellow)}
.body-copy{position:absolute;font-size:14px;line-height:21px;color:#222}
/* sections */
.heading-dark{position:absolute;font-weight:800;color:var(--ink)}
.heading-light{position:absolute;font-weight:800;color:var(--white);font-size:30px;line-height:41px}
.light-copy{position:absolute;color:var(--white);font-size:14px;line-height:22px}
.grid-bg{background-color:#fafafa;background-image:linear-gradient(#ececec 1px,transparent 1px),linear-gradient(90deg,#ececec 1px,transparent 1px);background-size:26px 26px}
.vertical{position:absolute;transform:rotate(-90deg);transform-origin:left top;font-weight:800;font-size:18px;color:var(--ink)}
.dots{position:absolute;display:flex;gap:10px}
.dots i{display:block;width:9px;height:9px;border-radius:50%;background:var(--ink)}
.dots i:first-child{background:var(--yellow)}
.circle-photo{position:absolute;border-radius:50%}
/* footer */
.footer{position:absolute;left:0;top:4117px;width:1200px;height:314px;background:var(--green);color:var(--white)}
.foot-brand{position:absolute;left:150px;top:62px;width:250px;color:var(--white);font-weight:500}
.foot-brand .name{display:block;font-size:34px;line-height:40px;letter-spacing:3px}
.foot-brand .tag{display:block;margin-top:6px;font-size:9px;line-height:13px;letter-spacing:1.4px}
.foot-col{position:absolute;top:60px;font-size:12px}
.foot-col h4{font-size:14px;font-weight:800;margin-bottom:16px}
.foot-col li{list-style:none;margin-bottom:14px;white-space:nowrap}
.social{display:flex;gap:6px}
.social i{display:block;width:31px;height:31px;border-radius:50%;border:2px solid var(--white)}
</style>
</head>
<body>

<!-- HERO -->
<section class="hero">
  <div class="photo" role="img" aria-label="Luxury home at dusk with illuminated stone walkway and landscape lights" style="inset:0;background:radial-gradient(ellipse at 60% 35%,rgba(255,190,90,.35),transparent 40%),radial-gradient(ellipse at 40% 80%,rgba(120,110,80,.5),transparent 50%)"></div>
  <div class="brand" style="left:43px;top:46px;flex-direction:column;align-items:flex-start;gap:2px">
    <span style="font-size:30px;letter-spacing:3px">CORWIN BEACON</span>
    <span style="font-size:11px;letter-spacing:1.6px">LIGHTING · RESIDENTIAL &amp; COMMERCIAL</span>
  </div>
  <nav class="nav">
    <span class="active">HOME</span><span>ABOUT US</span><span>PRODUCTS AND SERVICES</span><span>CONTACT US</span>
    <span style="display:flex;align-items:center;gap:8px;font-size:17px;font-weight:600">
      <svg width="20" height="20" viewBox="0 0 24 24" fill="none" stroke="#fff" stroke-width="2"><path d="M22 16.9v3a2 2 0 0 1-2.2 2 19.8 19.8 0 0 1-8.6-3.1 19.5 19.5 0 0 1-6-6A19.8 19.8 0 0 1 2.1 4.2 2 2 0 0 1 4.1 2h3a2 2 0 0 1 2 1.7c.1 1 .4 1.9.7 2.8a2 2 0 0 1-.5 2.1L8 9.9a16 16 0 0 0 6 6l1.3-1.3a2 2 0 0 1 2.1-.4c.9.3 1.8.6 2.8.7a2 2 0 0 1 1.7 2z"/></svg>
      +1 555 014 2290</span>
  </nav>
  <h1 class="hero-title" style="top:268px;font-size:64px;letter-spacing:1px">RESIDENTIAL</h1>
  <div class="hero-title" style="top:346px;font-size:38px">LANDSCAPE LIGHTING</div>
  <p class="hero-title" style="top:416px;font-size:22px;font-weight:400;line-height:30px">Illuminate Your Outdoors with Expert<br>Residential Landscape Lighting</p>
  <a class="btn" style="left:441px;top:503px;width:318px;height:50px;font-size:15px">Get your free estimate today!</a>
  <div class="abs" style="left:556px;top:617px;display:flex;gap:8px">
    <i style="width:16px;height:4px;background:#d61f2b;display:block"></i><i style="width:16px;height:4px;background:#fff;display:block"></i><i style="width:16px;height:4px;background:#fff;display:block"></i><i style="width:16px;height:4px;background:#fff;display:block"></i>
  </div>
</section>

<!-- INTRO -->
<section>
  <div class="photo" role="img" aria-label="Garden path lit by low bollard lights" style="left:150px;top:763px;width:320px;height:315px;background:linear-gradient(160deg,#2d3a2a,#6a5a3a 50%,#3b3a4a)"></div>
  <div class="photo" role="img" aria-label="Technician installing a landscape light in a garden bed" style="left:283px;top:945px;width:283px;height:316px;background:linear-gradient(170deg,#1f2a44,#3a3a3a 55%,#6a4a24);border:6px solid #fff"></div>
  <h2 class="intro-head">Illuminate with <span>Confidence.</span><br>Designed with <span>Precision.</span><br>Installed with <span>Care.</span></h2>
  <div class="rule" style="left:628px;top:894px"></div>
  <p class="body-copy" style="left:626px;top:922px;width:425px">Locally and veteran-owned, we take pride in transforming outdoor spaces through innovative lighting solutions tailored to your vision. From landscape and holiday lighting to permanent installations, our effortless process and expert design deliver breathtaking results and lasting curb appeal. Backed by a lifetime warranty and quarterly service options, our commitment to quality and customer satisfaction is unwavering.</p>
  <p class="body-copy" style="left:628px;top:1118px;width:425px;color:var(--green-dark);font-weight:700">Try before you buy and experience your home in a whole new light with our complimentary demo kit — see the stunning effects before you decide.</p>
  <a class="btn" style="left:631px;top:1212px;width:293px;height:46px">Get your free estimate today!</a>
</section>

<!-- WELCOME -->
<section class="abs" style="left:0;top:1329px;width:1200px;height:502px;background:var(--mist);overflow:hidden">
  <svg class="abs" style="left:0;top:0" width="1200" height="502" viewBox="0 0 1200 502">
    <path d="M710 0 C640 80 720 150 690 230 C660 330 620 420 740 440 C880 460 1020 420 1200 475 L1200 0 Z" fill="#f7b51a"/>
    <path d="M700 0 C630 80 710 150 680 230 C650 320 612 412 735 430 C880 450 1020 410 1200 465 L1200 0 Z" fill="#3b4a3a" role="img" aria-label="Modern home at twilight with curved illuminated driveway and flower beds"/>
  </svg>
  <h2 class="heading-dark" style="left:150px;top:60px;font-size:30px;line-height:41px">Welcome to<br>Corwin Beacon Lighting</h2>
  <p class="body-copy" style="left:150px;top:202px;width:447px;text-align:justify;font-size:13.5px;line-height:22px">Derek is retired Army and he opened a fitness studio in 2017 with his wife Jolene. He has installed low voltage lighting in every home he lived in and for his friends and family over the years and decided to open his own business because he is passionate about beautifying outdoor landscapes and highlighting a properties full potential, not only in the day but at night as well all while providing safety and security for his clients.</p>
  <a class="btn" style="left:150px;top:385px;width:135px;height:48px;font-size:13px">Read more</a>
</section>

<!-- FEATURED RESIDENTIAL -->
<section class="abs grid-bg" style="left:0;top:1831px;width:1200px;height:937px">
  <svg class="abs" style="left:0;top:0" width="1200" height="520"><polygon points="0,0 1200,0 1200,511 0,310" fill="#1d9371"/></svg>
  <svg class="abs" style="left:150px;top:55px" width="520" height="440" role="img" aria-label="Brick house with warm uplighting across a front lawn at dusk"><path d="M10 30 L60 12 L150 22 L260 6 L380 18 L500 8 L512 90 L505 200 L515 320 L500 400 L380 425 L260 432 L130 420 L20 410 L8 300 L16 170 Z" fill="#4d5638"/></svg>
  <h2 class="heading-light" style="left:735px;top:84px">Featured Residential<br>Lighting Project</h2>
  <div class="rule" style="left:737px;top:178px;background:#fff"></div>
  <p class="light-copy" style="left:736px;top:210px;width:310px">Lorem ipsum dolor sit amet, consectetur adipiscing elit, sed do eiusmod tempor incididunt ut labore et dolore magna aliqua. Ut enim ad minim veniam,</p>
  <a class="btn" style="left:737px;top:331px;width:216px;height:44px;font-size:13px">Residential portfolio</a>
  <div class="vertical" style="left:110px;top:735px">Recent Projects</div>
  <div class="photo" role="img" aria-label="Lit brick home at night" style="left:152px;top:552px;width:286px;height:208px;background:linear-gradient(180deg,#24304a,#5a4a34 60%,#4a5130)"></div>
  <div class="photo" role="img" aria-label="Lit brick home at dusk" style="left:459px;top:552px;width:286px;height:208px;background:linear-gradient(180deg,#3a3f40,#7a5a30 60%,#5a5a30)"></div>
  <div class="photo" role="img" aria-label="Home side facade with path lighting" style="left:766px;top:552px;width:286px;height:208px;background:linear-gradient(180deg,#1e2a48,#5a5548 60%,#2e3828)"></div>
  <div class="dots" style="left:576px;top:783px"><i></i><i></i><i></i></div>
  <div class="btn-outline" style="left:497px;top:827px;width:222px;height:44px">Residential portfolio</div>
</section>

<!-- FEATURED COMMERCIAL -->
<section class="abs grid-bg" style="left:0;top:2768px;width:1200px;height:928px">
  <svg class="abs" style="left:0;top:0" width="1200" height="520"><polygon points="0,0 1200,0 1200,310 0,517" fill="#1d9371"/></svg>
  <h2 class="heading-light" style="left:150px;top:95px">Featured Commercial<br>Lighting Project</h2>
  <div class="rule" style="left:152px;top:198px;background:#fff"></div>
  <p class="light-copy" style="left:150px;top:228px;width:310px">Lorem ipsum dolor sit amet, consectetur adipiscing elit, sed do eiusmod tempor incididunt ut labore et dolore magna aliqua. Ut enim ad minim veniam,</p>
  <a class="btn" style="left:150px;top:340px;width:216px;height:44px;font-size:13px">Commercial portfolio</a>
  <svg class="abs" style="left:505px;top:60px" width="560" height="415" role="img" aria-label="Stepping stone path lit by a bollard light through lavender and grasses"><path d="M20 20 L120 5 L260 15 L400 4 L540 18 L552 120 L545 250 L555 360 L520 405 L380 410 L240 402 L110 412 L12 395 L6 270 L16 140 Z" fill="#2c3a24"/></svg>
  <div class="vertical" style="left:110px;top:740px">Recent Projects</div>
  <div class="photo" role="img" aria-label="Lit garden bed with stone border" style="left:152px;top:557px;width:286px;height:208px;background:linear-gradient(180deg,#3a5a2a,#6a7a5a 60%,#4a7a30)"></div>
  <div class="photo" role="img" aria-label="Curved lawn edge with garden lights" style="left:459px;top:557px;width:286px;height:208px;background:linear-gradient(180deg,#2a3a2a,#4a5a30 60%,#3a6a2a)"></div>
  <div class="photo" role="img" aria-label="Boardwalk lined with bollard lights at night" style="left:766px;top:557px;width:286px;height:208px;background:linear-gradient(180deg,#151515,#2a2218 60%,#5a3a20)"></div>
  <div class="dots" style="left:576px;top:786px"><i></i><i></i><i></i></div>
  <div class="btn-outline" style="left:497px;top:834px;width:222px;height:44px">Commercial portfolio</div>
</section>

<!-- CTA -->
<section class="abs" style="left:0;top:3696px;width:1200px;height:421px;background:var(--ivory);overflow:hidden">
  <svg class="abs" style="left:0;top:0" width="1200" height="421" fill="none" stroke="#f3d27a" stroke-width="1.5">
    <ellipse cx="600" cy="420" rx="470" ry="480"/>
    <ellipse cx="600" cy="430" rx="520" ry="520"/>
  </svg>
  <div class="circle-photo" role="img" aria-label="Service member embracing family member" style="left:80px;top:80px;width:152px;height:152px;background:#6a6a4a"></div>
  <div class="circle-photo" role="img" aria-label="Family in front of their home" style="left:165px;top:264px;width:106px;height:106px;background:#7a6a5a"></div>
  <div class="circle-photo" role="img" aria-label="Illuminated home at night" style="left:972px;top:79px;width:154px;height:154px;background:#2a2e24"></div>
  <div class="circle-photo" role="img" aria-label="Path lights in a dark garden" style="left:931px;top:295px;width:108px;height:108px;background:#3a3530"></div>
  <h2 class="abs" style="left:0;width:1200px;text-align:center;top:78px;font-size:30px;line-height:41px;font-weight:800">Enhance Your Home with Professional<br>Residential Landscape Lighting</h2>
  <p class="abs" style="left:0;width:1200px;text-align:center;top:198px;font-size:28px;font-weight:400">We Offer Free Estimates &amp; <span style="background:var(--green);color:#fff;font-weight:800;padding:2px 10px">10% OFF</span></p>
  <p class="abs" style="left:0;width:1200px;text-align:center;top:244px;font-size:26px;font-weight:400">for Military, Veterans, and First Responders!</p>
  <a class="btn" style="left:435px;top:303px;width:318px;height:50px;font-size:15px">Get your free estimate today!</a>
</section>

<!-- FOOTER -->
<footer class="footer">
  <div class="foot-brand">
    <span class="name">CORWIN</span>
    <span class="name">BEACON</span>
    <span class="tag">LIGHTING · RESIDENTIAL<br>&amp; COMMERCIAL</span>
  </div>
  <div class="foot-col" style="left:450px">
    <h4>MENU</h4>
    <ul><li>Home</li><li>About Us</li><li>products and services</li><li>Contact Us</li></ul>
  </div>
  <div class="foot-col" style="left:630px">
    <h4>CONTACT US</h4>
    <div style="display:flex;gap:14px;align-items:center;margin-bottom:22px">
      <svg width="18" height="18" viewBox="0 0 24 24" fill="#fff"><path d="M22 16.9v3a2 2 0 0 1-2.2 2 19.8 19.8 0 0 1-8.6-3.1 19.5 19.5 0 0 1-6-6A19.8 19.8 0 0 1 2.1 4.2 2 2 0 0 1 4.1 2h3a2 2 0 0 1 2 1.7c.1 1 .4 1.9.7 2.8a2 2 0 0 1-.5 2.1L8 9.9a16 16 0 0 0 6 6l1.3-1.3a2 2 0 0 1 2.1-.4c.9.3 1.8.6 2.8.7a2 2 0 0 1 1.7 2z"/></svg>
      <span>Call us<br>+1 555 014 2290</span></div>
    <div style="display:flex;gap:14px;align-items:center">
      <svg width="18" height="14" viewBox="0 0 24 18" fill="#fff"><path d="M0 0h24v18H0z"/><path d="M0 0l12 9 12-9" stroke="#1d9371" stroke-width="2" fill="none"/></svg>
      <span>Email us<br>info@corwinbeacon.com</span></div>
  </div>
  <div class="foot-col" style="left:835px">
    <h4>FOLLOW US</h4>
    <div class="social"><i></i><i></i><i></i><i></i><i></i></div>
    <a class="btn" style="position:relative;margin-top:24px;width:212px;height:34px;font-size:10px">Get your free estimate today!</a>
  </div>
  <div class="abs" style="left:150px;top:222px;width:900px;height:1px;background:rgba(255,255,255,.7)"></div>
  <p class="abs" style="left:0;width:1200px;top:262px;text-align:center;font-size:11px">Copyright © 2025 All Rights Reserved</p>
</footer>

</body>
</html>
```